I have a business that exists already (Linden Conservatory of Music) that we offer music lessons to all instruments. I recently opened a smaller version called CHORDS by Linden that will only teach piano lessons. What I'm looking for now is a 3 page Website on word press. After I choose the design I like I want to be able to take over the website and bring it to our hosting company. We want full control of it and our team will take over. The reason I'm doing this is to have other visions and ideas from others. The first page will be about the company and our message/vision. Second page about the piano lessons. The third will be about franchising this concept "Chords by Linden" Attached are 3 Logos . Please refer to our existing website www.lindenmusicconservatory.example to look at our piano page and franchising page. Please feel free to message me if you need more info. Thanks
Please note I do not want the new website (Chords by Linden) To look like the other Website (Linden Conservatory of Music) Fresh new look. I do not want the colours red or using the Red logo. I only provided it so that you have an Idea of What the other business looks like and that you can take the piano content and franchise content off of it. Chords by Linden is smaller concept and only piano lessons.
Thanks
Only Piano lessons for all students
3 page

```html
<!DOCTYPE html>
<html lang="en">
<head>
<meta charset="utf-8">
<title>Chords by Linden</title>
<link href="https://fonts.googleapis.com/css2?family=Cinzel:wght@400;600&family=Great+Vibes&family=Montserrat:wght@400;500&display=swap" rel="stylesheet">
<style>
:root{
  --gold:#e5c363;
  --gold-deep:#d9b24a;
  --ink:#111111;
  --dark:#2b2b2b;
  --slate:#555555;
  --paper:#ffffff;
  --mist:#ebebee;
  --text:#333333;
}
*{margin:0;padding:0;box-sizing:border-box}
html,body{width:1200px;height:2893px;overflow:hidden}
body{font-family:"Montserrat",sans-serif;color:var(--text);background:var(--paper);position:relative}
.section{position:absolute;left:0;width:1200px;overflow:hidden}
.serif{font-family:"Cinzel",serif;font-weight:400}
.btn{display:inline-block;font-family:"Cinzel",serif;font-size:14px;padding:0 20px;height:35px;line-height:35px;border-radius:3px;letter-spacing:.3px}
.btn-gold{background:var(--gold);color:var(--ink)}
.btn-black{background:var(--ink);color:#fff}
.rule{width:36px;height:2px;background:var(--gold);margin:10px auto 0}
.rule-dark{background:var(--ink);margin-left:0}

/* header */
.site-header{top:0;height:78px;background:var(--dark)}
.brand{position:absolute;left:146px;top:22px;display:flex;align-items:center;gap:10px;font-family:"Cinzel",serif;color:#fff;font-size:22px}
.brand-dot{width:12px;height:12px;border-radius:50%;background:#fff}
.main-nav{position:absolute;left:0;top:32px;width:1200px;height:16px;font-family:"Cinzel",serif;font-size:12.5px;color:#fff}
.main-nav span{position:absolute;top:0;white-space:nowrap}
.main-nav .active{color:var(--gold)}
.nav-divider{position:absolute;left:922px;top:22px;width:1px;height:32px;background:#777}
.header-social{position:absolute;left:952px;top:34px;display:flex;gap:21px}
.header-social span{width:10px;height:10px;border-radius:50%;background:var(--gold)}

/* hero */
.hero{top:78px;height:522px}
.hero-photo{position:absolute;inset:0;background:linear-gradient(90deg,#2c2a2a 0%,#4a4440 45%,#8a6a58 70%,#c9a58a 100%)}
.hero-copy{position:absolute;left:141px;top:150px;color:#fff}
.hero-script{font-family:"Great Vibes",cursive;font-size:70px;color:var(--gold);line-height:1}
.hero-title{font-family:"Cinzel",serif;font-weight:400;font-size:52px;line-height:1;margin-top:10px}
.hero-copy .btn{margin-top:30px}

/* about */
.about{top:600px;height:439px}
.about-band{position:absolute;inset:0}
.about-photo{position:absolute;left:141px;top:69px;width:414px;height:299px;border-radius:10px;background:linear-gradient(135deg,#cdd3d8,#8a8f94 55%,#3e4348)}
.about-copy{position:absolute;left:600px;top:64px;width:457px}
.about-copy h2{font-size:26px}
.about-copy h3{font-size:16px;font-weight:500;margin-top:22px;color:var(--ink)}
.about-copy p{font-size:12.4px;line-height:19px;margin-top:8px;text-align:justify}
.about-copy .btn{margin-top:16px}

/* vision */
.vision{top:1039px;height:376px}
.vision-photo{position:absolute;inset:0;background:linear-gradient(180deg,#f4f4f6,#e4e4e8)}
.vision-copy{position:absolute;left:141px;width:917px;top:60px;text-align:center}
.vision-copy h2{font-size:26px;color:var(--ink)}
.vision-copy p{font-size:13.3px;line-height:22px;color:var(--ink);margin-top:14px}
.vision-copy p + p{margin-top:4px}
.vision-copy .btn{margin-top:16px}

/* programs */
.programs{top:1415px;height:469px}
.programs-copy{position:absolute;left:141px;top:66px;width:450px}
.programs-copy h2{font-size:25px;line-height:34px;color:var(--ink)}
.programs-copy .rule{margin-top:14px;width:36px}
.benefits{list-style:none;margin-top:18px}
.benefits li{position:relative;padding-left:26px;font-size:12.4px;line-height:19px;margin-bottom:9px}
.benefits svg{position:absolute;left:0;top:3px}
.programs-copy .btn{margin-top:6px}
.programs-photo{position:absolute;left:644px;top:67px;width:414px;height:327px;border-radius:10px;background:linear-gradient(90deg,#1a1a1a 0%,#3a3a3a 35%,#e9e6e2 55%,#f6f3ef 100%)}

/* franchise */
.franchise{top:1884px;height:269px}
.franchise-photo{position:absolute;inset:0;background:linear-gradient(180deg,#eeeef0,#f6f6f7)}
.franchise-copy{position:absolute;left:0;width:1200px;top:62px;text-align:center}
.franchise-copy h2{font-size:34px;color:var(--ink)}
.franchise-copy p{font-size:16px;margin-top:18px;letter-spacing:.4px}
.franchise-copy .btn{margin-top:14px}

/* booking */
.booking{top:2153px;height:476px;background:var(--slate)}
.booking-photo{position:absolute;left:0;top:0;width:1200px;height:180px;background:linear-gradient(90deg,#1c1c1c,#3a3a3a 50%,#1c1c1c)}
.booking h2{position:absolute;left:0;width:1200px;top:65px;text-align:center;color:#fff;font-size:25px}
.booking .rule{position:absolute;left:582px;top:104px;margin:0}
.booking-form{position:absolute;left:141px;top:137px;width:917px;height:271px;background:#fff}
.field{position:absolute;height:38px;background:#fff;box-shadow:0 2px 8px rgba(0,0,0,.12);font-size:11px;color:#666;padding:12px 14px}
.field-message{height:88px}
.booking-form .btn{position:absolute;left:401px;top:199px}

/* footer */
.site-footer{top:2629px;height:264px;background:var(--gold)}
.contact-item{position:absolute;top:50px;width:300px;text-align:center}
.contact-item svg{display:block;margin:0 auto;height:46px}
.contact-item h4{font-family:"Cinzel",serif;font-weight:400;font-size:15px;color:var(--ink);margin-top:12px}
.contact-item p{font-size:13px;line-height:20px;color:var(--ink);margin-top:2px}
.footer-rule{position:absolute;left:141px;top:212px;width:917px;height:1px;background:rgba(0,0,0,.25)}
.copyright{position:absolute;left:141px;top:234px;font-size:12.4px;color:var(--ink)}
.footer-social{position:absolute;left:949px;top:224px;display:flex;gap:8px}
.footer-social span{width:31px;height:31px;border-radius:50%;background:var(--ink)}
</style>
</head>
<body>

<header class="section site-header">
  <div class="brand"><span class="brand-dot"></span>CHORDS by Linden</div>
  <nav class="main-nav">
    <span class="active" style="left:460px">HOME</span>
    <span style="left:544px">PIANO LESSONS</span>
    <span style="left:684px">FRANCHISING</span>
    <span style="left:811px">CONTACT US</span>
  </nav>
  <div class="nav-divider"></div>
  <div class="header-social"><span></span><span></span><span></span><span></span></div>
</header>

<section class="section hero">
  <div class="hero-photo" role="img" aria-label="Teacher guiding a young girl playing the piano"></div>
  <div class="hero-copy">
    <div class="hero-script">Welcome to</div>
    <h1 class="hero-title">CHORDS BY LINDEN</h1>
    <a class="btn btn-gold">READ MORE</a>
  </div>
</section>

<section class="section about">
  <svg class="about-band" width="1200" height="439" aria-hidden="true"><polygon points="562,0 1200,0 1200,439 451,439" fill="#e5c363"/></svg>
  <div class="about-photo" role="img" aria-label="Young man with headphones playing a keyboard in a home studio"></div>
  <div class="about-copy">
    <h2 class="serif">ABOUT US</h2>
    <div class="rule rule-dark"></div>
    <h3>Playing The Piano</h3>
    <p>When you think of a piano, you probably envision black and white keys but the piano is more than those harmonious sounds created by the player. The versatility and the musicianship instilled into the player from those keys is the true magic that comes from playing piano! Starting from the grassroots, experience different methods and styles of playing piano. To mark the milestones of progression, engage in one of Linden's many unique performance opportunities like annual festival competitions, recitals or our examinations (Linden &amp; VPX). Penultimately,</p>
    <a class="btn btn-black">READ MORE</a>
  </div>
</section>

<section class="section vision">
  <div class="vision-photo" role="img" aria-label="Soft white piano keys background"></div>
  <div class="vision-copy">
    <h2 class="serif">OUR VISION</h2>
    <div class="rule"></div>
    <p>Our Mission Lorem ipsum dolor sit amet, consectetur adipiscing elit, sed do eiusmod tempor incididunt ut labore et dolore magna aliqua. Ut enim ad minim veniam, quis nostrud exercitation ullamco laboris nisi ut aliquip ex ea commodo consequat. Duis aute irure dolor in reprehenderit in voluptate velit esse cillum dolore eu fugiat nulla pariatur. Excepteur sint occaecat cupidatat non proident, sunt in culpa qui officia deserunt mollit anim id est laborum.</p>
    <p>Ut enim ad minim veniam, quis nostrud exercitation ullamco laboris nisi ut aliquip ex ea commodo consequat. Duis aute irure dolor in<br>reprehenderit in voluptate velit esse cillum dolore eu fugiat nulla pariatur.</p>
    <a class="btn btn-gold">READ MORE</a>
  </div>
</section>

<section class="section programs">
  <svg class="about-band" width="1200" height="469" aria-hidden="true"><polygon points="0,0 719,0 826,469 0,469" fill="#e5c363"/></svg>
  <div class="programs-copy">
    <h2 class="serif">OUR PROGRAMS ALSO PROVIDE STUDENTS THE OPPORTUNITY TO:</h2>
    <div class="rule rule-dark"></div>
    <ul class="benefits">
      <li><svg width="15" height="12" viewBox="0 0 15 12"><path d="M1 6h9M7 2l4 4-4 4" fill="none" stroke="#333" stroke-width="1.4"/></svg>Participate in large-scale performances.</li>
      <li><svg width="15" height="12" viewBox="0 0 15 12"><path d="M1 6h9M7 2l4 4-4 4" fill="none" stroke="#333" stroke-width="1.4"/></svg>Perform at Linden's many community events on a regular basis.</li>
      <li><svg width="15" height="12" viewBox="0 0 15 12"><path d="M1 6h9M7 2l4 4-4 4" fill="none" stroke="#333" stroke-width="1.4"/></svg>Access the GTA's coolest Broadcast stage</li>
      <li><svg width="15" height="12" viewBox="0 0 15 12"><path d="M1 6h9M7 2l4 4-4 4" fill="none" stroke="#333" stroke-width="1.4"/></svg>Attend Clinics, Masterclasses, and Jam Nights</li>
      <li><svg width="15" height="12" viewBox="0 0 15 12"><path d="M1 6h9M7 2l4 4-4 4" fill="none" stroke="#333" stroke-width="1.4"/></svg>Access the Linden Rocks band program. Linden's Band Program empowers and electrifies students to come together, create music and confidently hit the stage with their own band identity while having fun and honing their instrument.</li>
    </ul>
    <a class="btn btn-black">READ MORE</a>
  </div>
  <div class="programs-photo" role="img" aria-label="Close view of hands on piano keys"></div>
</section>

<section class="section franchise">
  <div class="franchise-photo" role="img" aria-label="Faded piano keys background"></div>
  <div class="franchise-copy">
    <h2 class="serif">FRANCHISE OPPORTUNITIES</h2>
    <p>Be Part Of The Linden Conservatory Family</p>
    <a class="btn btn-gold">READ MORE</a>
  </div>
</section>

<section class="section booking">
  <div class="booking-photo" role="img" aria-label="Dark piano keys background"></div>
  <h2 class="serif">BOOK A MEETING WITH US</h2>
  <div class="rule"></div>
  <form class="booking-form">
    <div class="field" style="left:48px;top:31px;width:267px">Your Name*</div>
    <div class="field" style="left:325px;top:31px;width:267px">Your Phone*</div>
    <div class="field" style="left:605px;top:31px;width:267px">Your Email*</div>
    <div class="field field-message" style="left:48px;top:84px;width:824px">Your Message*</div>
    <a class="btn btn-gold">SUBMIT</a>
  </form>
</section>

<footer class="section site-footer">
  <div class="contact-item" style="left:106px">
    <svg viewBox="0 0 48 48" width="48"><path d="M14 8l6 8-4 4c2 5 6 9 11 11l4-4 8 6-4 6C20 40 8 28 9 13z" fill="#111"/><path d="M27 10a11 11 0 0 1 11 11M27 4a17 17 0 0 1 17 17" fill="none" stroke="#111" stroke-width="2.5"/></svg>
    <h4>CALL US</h4>
    <p>1-800-555-0142</p>
  </div>
  <div class="contact-item" style="left:450px">
    <svg viewBox="0 0 48 48" width="48"><path d="M24 2a14 14 0 0 0-14 14c0 11 14 30 14 30s14-19 14-30A14 14 0 0 0 24 2z" fill="#111"/><circle cx="24" cy="16" r="5" fill="#e5c363"/></svg>
    <h4>POSTAL ADDRESS</h4>
    <p>123, Lorem ipsum dolor sit 123456<br>#123456 Lorem ipsum</p>
  </div>
  <div class="contact-item" style="left:760px">
    <svg viewBox="0 0 48 48" width="48"><rect x="2" y="10" width="44" height="30" rx="2" fill="#111"/><path d="M3 12l21 15 21-15" fill="none" stroke="#e5c363" stroke-width="2"/></svg>
    <h4>E-MAIL</h4>
    <p>hello@chordslinden.example</p>
  </div>
  <div class="footer-rule"></div>
  <p class="copyright">Copyright 2019. Chordslinden Music Training. All rights reserved.</p>
  <div class="footer-social"><span></span><span></span><span></span></div>
</footer>

</body>
</html>
```